Business Card for a mobile physiotherapy company

I need a layout for a business card for a mobile physiotherapy company.
Slogan is "Mobile Physiotherapy - Your Road To Recovery"
Phone number is 867-555-0142
Email VardenTherapy@postnest.ca (subject to change with website)
Website www.VardenTherapy.ca
My name and credentials: Luke Varden Luke Varden, BSc(kin), MPT, CAFCI, IMS
Information maybe included: Direct Billing, Services including Physiotherapy, IMS, acupuncture
Maybe include facebook and instagram logos
One side with the logo clean and sharp
Other side with details, try not to look too busy, keep everything concise

```html
<!DOCTYPE html>
<html lang="en">
<head>
<meta charset="utf-8">
<title>Varden Therapy Business Card</title>
<link rel="stylesheet" href="https://fonts.googleapis.com/css2?family=Merriweather:wght@700&family=Lora:wght@400;500&display=swap">
<style>
  :root {
    --backdrop: #b8b8b8;
    --card: #f4f4f2;
    --navy: #244670;
    --green: #1d5a47;
    --text: #2b3a55;
  }
  * { box-sizing: border-box; margin: 0; padding: 0; }
  html, body { width: 1200px; height: 576px; overflow: hidden; }
  body { background: var(--backdrop); position: relative; font-family: "Lora", Georgia, serif; color: var(--text); }
  .card {
    position: absolute; top: 138px; height: 292px; background: var(--card);
    border-radius: 12px; overflow: hidden; box-shadow: 0 3px 6px rgba(0,0,0,.25);
  }
  .card-front { left: 82px; width: 484px; }
  .card-back { left: 602px; width: 480px; }

  .wordmark {
    position: absolute; display: flex; align-items: center;
    font-family: "Lora", Georgia, serif; font-weight: 500; color: var(--navy);
    line-height: 1; white-space: nowrap;
  }
  .wordmark-dot { border-radius: 50%; background: var(--navy); flex: none; }

  .front-wordmark { top: 108px; left: 0; width: 100%; justify-content: center; gap: 14px; font-size: 38px; }
  .front-wordmark .wordmark-dot { width: 26px; height: 26px; }

  .services { position: absolute; bottom: 20px; left: 0; width: 100%; text-align: center; font-size: 12.5px; color: var(--navy); }
  .front-strip { position: absolute; left: 0; bottom: 0; width: 100%; height: 6px; background: linear-gradient(90deg, var(--green), var(--navy)); }

  .back-wordmark { top: 36px; left: 25px; gap: 10px; font-size: 26px; }
  .back-wordmark .wordmark-dot { width: 18px; height: 18px; }

  .slogan { position: absolute; top: 83px; left: 25px; font-size: 12.3px; font-weight: 500; color: var(--navy); }
  .person-name { position: absolute; top: 127px; left: 25px; font-family: "Merriweather", Georgia, serif; font-weight: 700; font-size: 19px; color: var(--navy); letter-spacing: .5px; }
  .credentials { position: absolute; top: 155px; left: 25px; font-size: 11px; }
  .follow { position: absolute; top: 172px; left: 25px; font-size: 12.5px; display: flex; align-items: center; gap: 6px; }
  .social-dot { width: 20px; height: 20px; border-radius: 50%; background: var(--navy); display: inline-block; }
  .contacts { position: absolute; top: 211px; left: 25px; list-style: none; font-size: 12.8px; }
  .contacts li { display: flex; align-items: center; gap: 14px; height: 17.5px; }
  .contacts svg { width: 10px; height: 10px; fill: var(--text); }
  .motif { position: absolute; right: 0; top: 0; width: 150px; height: 100%; background: linear-gradient(160deg, #2b5282, var(--navy)); }
</style>
</head>
<body>
  <section class="card card-front">
    <div class="wordmark front-wordmark"><span class="wordmark-dot"></span>Varden Therapy</div>
    <p class="services">Direct Billing &nbsp;|&nbsp; Services Including Physiotherapy &nbsp;|&nbsp; IMS &nbsp;|&nbsp; Acupuncture</p>
    <div class="front-strip"></div>
  </section>

  <section class="card card-back">
    <div class="wordmark back-wordmark"><span class="wordmark-dot"></span>Varden Therapy</div>
    <p class="slogan">Mobile Physiotherapy - Your Road To Recovery</p>
    <h1 class="person-name">LUKE VARDEN</h1>
    <p class="credentials">BSc(kin), MPT, CAFCI, IMS</p>
    <p class="follow">Follow us on: <span class="social-dot"></span><span class="social-dot"></span></p>
    <ul class="contacts">
      <li><svg viewBox="0 0 10 10"><path d="M1 3c0-1 1-2 4-2s4 1 4 2v1H7V3H3v1H1zM2 5h6l1 4H1z"/></svg>867-555-0142</li>
      <li><svg viewBox="0 0 10 10"><path d="M0 2h10v6H0zM1 3l4 3 4-3v-.2H1z" fill-rule="evenodd"/></svg>VardenTherapy@postnest.ca</li>
      <li><svg viewBox="0 0 10 10"><circle cx="5" cy="5" r="4.5"/></svg>www.VardenTherapy.ca</li>
    </ul>
    <div class="motif" role="img" aria-label="Large decorative brand motif in navy"></div>
  </section>
</body>
</html>
```